Schlichtes Design für Malerbetrieb
Zielgruppe
Wir sind ein mittelgroßer Malerbetrieb in München mit umfangreichem Leistungsspektrum.
Unsere Hauptleistungen sind: Fassadenrenovierung, Altbausanierung, Betoninstandsetzung, Balkonabdichtung (kein Neubau!).
Unsere Zielgruppen sind: Hausverwaltungen, Firmen und Privatpersonen.
Unsere Kunden schätzen: Konstruktive Organisation und Planung im Vorfeld, Zuverlässigkeit, saubere Arbeitsweise, dauerhafte Balkonabdichtungen.
Aufgabenstellung
Wir möchten eine langlebige, stilvolle, minimalistische Homepage.
Wir möchten von der bestehenden Homepage nur die Schriftart für unseren Firmennamen (Century Gothic) und wenn möglich (nicht zwingend), irgendwo das florale Muster einbauen. Corporate-Design haben wir nicht.
Farbtöne: Firmennamen Orange (hellorange bis erdiges Orange möglich, da sind wir nicht fixiert) , einen dunklen Hintergrundfarbton (Petrol-Blaugrau ?) mit gelbem (neon bis senfgelb) Akzent (Linien), Blumenmuster weiß, grau.
Dies sind nur unsere Ideen. Wir sind aber auch absolut offen für eure Profi-Ideen.
Wir möchten uns von den unzähligen langweiligen 'Pinselseiten mit veralteten Bilder' unserer Kollegen interessant und mit Stil abheben.
Eher nach dem Motto 'weniger ist mehr'.
Einen positiven, sympathischen Eindruck geben und unsere Leistungen in den Vordergrund bringen.
Da wir viele Stammkunden haben, betreiben wir kein Social-Media und möchten dies vorerst auch nicht tun.
Die Seite wird in den nächsten Jahren nicht verändert, höchstens die Bilder aktualisiert.
Die Texte haben wir alle selbst entworfen und möchten wir so übernehmen.
Die Galerien sollen unkompliziert anzuschauen sein.
Uns gefällt die Struktur und Schlichtheit von https://vaartmolen.nl/ oder Timbra.de gut und wir mögen Vintage-Grafiken gerne.
Einerseits darf die Seite geradlinig, andererseits aber auch rund und floral wirken.

```html
<!DOCTYPE html>
<html lang="de">
<head>
<meta charset="utf-8">
<title>kolbrit – Malerarbeiten</title>
<link rel="stylesheet" href="https://fonts.googleapis.com/css2?family=Questrial&family=Roboto+Condensed:wght@400;700&family=Arimo:wght@400&display=swap">
<style>
  :root {
    --bg-pattern: #59595b;
    --bg-pattern-light: #646466;
    --panel: #3f3f41;
    --orange: #f2ac35;
    --yellow: #f6b32b;
    --text: #ffffff;
    --text-soft: #f1f1f1;
  }
  * { margin: 0; padding: 0; box-sizing: border-box; }
  html, body { width: 1200px; height: 900px; overflow: hidden; }
  body { position: relative; background: var(--bg-pattern); font-family: "Arimo", Arial, sans-serif; color: var(--text); }

  .backdrop { position: absolute; inset: 0; background: radial-gradient(circle at 30% 20%, var(--bg-pattern-light), var(--bg-pattern) 60%); }

  .brand { position: absolute; left: 111px; top: 38px; font-family: "Questrial", sans-serif; font-size: 54px; line-height: 1; color: var(--orange); letter-spacing: 1px; }

  .main-nav { position: absolute; left: 111px; right: 13px; top: 115px; display: flex; justify-content: space-between; font-family: "Roboto Condensed", sans-serif; font-size: 25px; }
  .main-nav a { color: var(--text); text-decoration: none; }

  .content-panel { position: absolute; left: 0; top: 156px; width: 1200px; height: 678px; background: var(--panel); border-top-left-radius: 110px 110px; border-bottom-right-radius: 110px 90px; }

  .page-title { position: absolute; left: 111px; top: 220px; font-family: "Questrial", sans-serif; font-size: 24px; font-weight: 400; color: var(--orange); }

  .gallery { position: absolute; left: 0; top: 273px; width: 1200px; height: 261px; background: var(--yellow); }
  .gallery .photo { position: absolute; top: 0; height: 261px; }
  .photo-a { left: 0; width: 447px; background: linear-gradient(180deg, #b9c6d6 0%, #d8d4d2 30%, #b8b3b4 65%, #6f7a4e 100%); }
  .photo-b { left: 497px; width: 275px; background: linear-gradient(90deg, #d8b08a 0%, #e2c0a0 55%, #8dbde0 100%); }
  .photo-c { left: 790px; width: 410px; background: linear-gradient(180deg, #c9cbcf 0%, #d3d3d5 50%, #a6a7a9 100%); }

  .gallery-arrow { position: absolute; top: 548px; width: 26px; height: 18px; }
  .gallery-arrow.prev { left: 17px; }
  .gallery-arrow.next { left: 1158px; }

  .copy { position: absolute; top: 571px; font-size: 13px; line-height: 21.6px; color: var(--text-soft); }
  .copy p + p { margin-top: 21.6px; }
  .copy-left { left: 111px; width: 500px; }
  .copy-right { left: 634px; width: 500px; }

  .footer-nav { position: absolute; top: 849px; left: 762px; display: flex; gap: 16px; font-family: "Roboto Condensed", sans-serif; font-size: 25px; }
  .footer-nav a { color: var(--text); text-decoration: none; }
  .footer-nav a.current { font-weight: 700; }
</style>
</head>
<body>
  <div class="backdrop" role="img" aria-label="Florales Ornamentmuster in Grautönen als Hintergrund"></div>

  <div class="brand">kolbrit</div>

  <nav class="main-nav">
    <a href="#">malerarbeiten</a>
    <a href="#">betoninstandsetzung</a>
    <a href="#">balkonabdichtung</a>
    <a href="#">farbgestaltung</a>
    <a href="#">wärmedämmung</a>
    <a href="#">ausbildung</a>
    <a href="#">portrait</a>
  </nav>

  <main class="content-panel"></main>

  <h1 class="page-title">Malerarbeiten</h1>

  <section class="gallery">
    <div class="photo photo-a" role="img" aria-label="Foto: sanierte Altbaufassade mit Erkern und Bäumen"></div>
    <div class="photo photo-b" role="img" aria-label="Foto: Erkerturm einer renovierten Altbaufassade vor blauem Himmel"></div>
    <div class="photo photo-c" role="img" aria-label="Foto: helle Altbaufassade mit Balkonen"></div>
  </section>

  <svg class="gallery-arrow prev" viewBox="0 0 26 18" aria-label="Zurück">
    <path d="M24 9H3M10 2 3 9l7 7" fill="none" stroke="var(--yellow)" stroke-width="3" stroke-linecap="round" stroke-linejoin="round"/>
  </svg>
  <svg class="gallery-arrow next" viewBox="0 0 26 18" aria-label="Weiter">
    <path d="M2 9h21M16 2l7 7-7 7" fill="none" stroke="var(--yellow)" stroke-width="3" stroke-linecap="round" stroke-linejoin="round"/>
  </svg>

  <div class="copy copy-left">
    <p>Flächen, die einheitlich und streifenlos erscheinen, erfreuen den Betrachter.<br>
    Sie unterstützen primär die optische Erscheinung eines Objekts.<br>
    Auf längere Zeit gesehen leisten Anstriche jedoch weitere wesentliche Dienste.<br>
    Sie schützen Ihr Gebäude oder Ihre Wohnung vor Witterungseinflüssen,<br>
    mechanischer Beschädigung und dem Nagen der Zeit. Unsere Tätigkeit<br>
    und unser Fachwissen schützen Ihren Besitz.</p>
    <p>Bei der Erstellung von baulichen Schutzmaßnahmen müssen alle Objekt-<br>
    gegebenheiten mit einbezogen werden. Um einen dauerhaften Bestand von<br>
    Objekten zu gewährleisten, muss jeder Beteiligte über das eigene<br>
    Aufgabengebiet hinweg denken.</p>
  </div>

  <div class="copy copy-right">
    <p>Wir betrachten bei der Ausarbeitung unserer Leistungen jedes Bauteil<br>
    gesondert mit seinen Eigenschaften. Die stets erneuerten Technologien<br>
    von Anstrichmitteln in Bezug auf Oberflächenbeschaffenheit,<br>
    Umweltverträglichkeit und Beständigkeit setzen wir jederzeit optimal ein.<br>
    Nur Fachleute suchen nach Ursachen und erarbeiten die richtigen Lösungen.</p>
  </div>

  <nav class="footer-nav">
    <a href="#" class="current">Kontakt</a>
    <a href="#">Impressum</a>
    <a href="#">Datenschutz</a>
  </nav>
</body>
</html>
```